Real Estate Webpage Design

We have an existing website: ferndaleestatecollective.com.au
We focus customised service mainly on Property Management and second-hand property sales.
We are not entirely happy about the current design and layout can stay roughly the same as the back end coding is linked to a CRM system.
We would like to see the design are more reachable to our clients and appearing.
Please check our Website Design Draft for more details.

Industry/Entity Type

Real estate Agency

Number of Pages Required

5+ page

Font styles to use
Sans Serif

Colors

Designer to choose colors to be used in the design.

```html
<!DOCTYPE html>
<html lang="en">
<head>
<meta charset="utf-8">
<title>Ferndale Estate Collective</title>
<link href="https://fonts.googleapis.com/css2?family=Teko:wght@500;600&family=Roboto:wght@400;500;700&display=swap" rel="stylesheet">
<style>
:root{
  --gold:#e8bd55;
  --navy:#243447;
  --ink:#1d1d1d;
  --text:#2b2b2b;
  --muted:#9a9a9a;
  --white:#ffffff;
}
*{margin:0;padding:0;box-sizing:border-box}
html,body{width:1200px;height:3051px;overflow:hidden}
body{position:relative;background:var(--white);font-family:"Roboto",sans-serif;color:var(--text)}
.abs{position:absolute}
.display{font-family:"Teko",sans-serif;font-weight:600;text-transform:uppercase;line-height:.9}

/* header */
.site-header{left:0;top:0;width:1200px;height:85px;border-top:4px solid var(--gold);background:var(--white)}
.brand{left:111px;top:18px;display:flex;align-items:center;gap:12px}
.brand-mark{width:44px;height:44px;background:var(--gold)}
.brand-name{font-family:"Roboto",sans-serif;font-weight:700;font-size:24px;color:var(--navy);line-height:1}
.main-nav{left:425px;top:34px;display:flex;gap:25px;font-size:14px;font-weight:700;color:#222}
.main-nav .active{color:var(--gold);border-bottom:3px solid var(--gold);padding-bottom:2px}
.search-btn{left:1049px;top:24px;width:40px;height:40px;border-radius:50%;background:var(--gold)}

/* hero */
.hero-title{left:0;width:1200px;top:228px;text-align:center;color:var(--white)}
.hero-title .big{font-size:150px;display:block}
.hero-title .small{font-size:74px;display:block;margin-top:-10px}
.hero-btn{left:522px;top:429px;width:156px;height:44px;border-radius:22px;background:var(--gold);color:var(--navy);font-family:"Teko",sans-serif;font-size:20px;font-weight:500;display:flex;align-items:center;justify-content:center}
.slide-arrow{width:48px;height:48px;border-radius:50%;background:#111;top:336px}

/* about */
.about-copy{left:654px;top:795px;width:434px}
.about-copy h2{font-size:62px;color:#1f1f1f;margin-bottom:18px}
.about-copy p{font-size:14.5px;line-height:21.5px;text-align:justify;color:#222;margin-bottom:21px}
.learn-btn{display:inline-block;background:#111;color:var(--white);border-radius:20px;padding:10px 21px 6px;font-family:"Teko",sans-serif;font-size:19px}

/* listings */
.listing-title{left:0;width:1200px;top:1428px;text-align:center;color:var(--white);font-size:60px}
.filter-tabs{left:0;width:1200px;top:1560px;display:flex;justify-content:center;gap:43px;font-size:14px;font-weight:700;color:var(--white)}
.filter-tabs .active{color:var(--gold);border-bottom:3px solid var(--gold);padding:0 4px 4px}
.listing-panel{left:111px;top:1604px;width:976px;height:500px;background:var(--white)}
.listing-card{top:1623px;width:463px;height:465px}
.listing-photo{width:463px;height:303px}
.listing-info{height:162px;background:var(--gold);text-align:center;padding-top:22px}
.listing-info h3{font-size:21.5px;font-weight:700;color:#2a2a2a;line-height:30px;text-transform:uppercase}
.listing-stats{display:flex;justify-content:space-around;margin-top:20px;padding:0 30px;font-size:21px;font-weight:700;color:#2a2a2a}
.listing-stats span{display:flex;align-items:center;gap:6px}

/* testimonials */
.testimonials-title{left:0;width:1200px;top:2172px;text-align:center;color:var(--navy);font-size:64px}
.quote-side{top:2273px;width:300px;font-size:14px;line-height:26px;color:var(--muted);opacity:.7;text-align:center;overflow:hidden;height:130px}
.quote-card{left:244px;top:2245px;width:711px;height:225px;background:var(--white);box-shadow:0 2px 14px rgba(0,0,0,.12);border-bottom:4px solid var(--gold);text-align:center;padding:26px 50px 0}
.quote-card p{font-size:14.2px;line-height:26px;color:#333}
.quote-card h4{margin-top:14px;font-size:20px;font-weight:700;color:var(--navy)}

/* footer */
.newsletter{left:374px;top:2657px;width:452px;height:44px;border-radius:22px;background:var(--white);border:2px solid var(--gold)}
.newsletter span{position:absolute;left:35px;top:12px;font-size:13.5px;color:#777}
.newsletter .sub-btn{left:auto;right:0;top:0;width:150px;height:40px;border-radius:20px;background:var(--gold);color:var(--navy);font-weight:700;font-size:14px;display:flex;align-items:center;justify-content:center;position:absolute}
.footer-col{top:2760px;color:var(--white)}
.footer-col h5{font-size:21px;font-weight:700;margin-bottom:18px}
.footer-col li{list-style:none;font-size:14.5px;line-height:28.5px;display:flex;gap:14px}
.footer-divider{top:2765px;width:1px;height:147px;background:rgba(255,255,255,.5)}
.social{width:38px;height:38px;border-radius:50%;border:1.5px solid var(--white);top:2805px}
.copyright{left:0;width:1200px;top:2984px;text-align:center;color:var(--white);font-size:14.5px}
</style>
</head>
<body>

<svg class="abs" style="left:0;top:0" width="1200" height="3051" aria-hidden="true">
  <polygon points="600,685 1200,643 1200,1277 600,1318" fill="#e8bd55"/>
  <polygon points="0,1362 600,1318 1200,1277 1200,1816 0,1816" fill="#243447"/>
  <polygon points="0,2614 1200,2529 1200,3051 0,3051" fill="#243447"/>
</svg>

<svg class="abs" style="left:0;top:85px" width="1200" height="643" role="img" aria-label="Photo of a brick-roofed family home with garden path under blue sky">
  <defs><linearGradient id="heroTone" x1="0" y1="0" x2="0" y2="1">
    <stop offset="0" stop-color="#3f6fc4"/><stop offset=".4" stop-color="#7c8c8a"/><stop offset=".7" stop-color="#8b7358"/><stop offset="1" stop-color="#a89578"/>
  </linearGradient></defs>
  <polygon points="0,0 1200,0 1200,555 0,643" fill="url(#heroTone)"/>
</svg>

<header class="abs site-header">
  <div class="abs brand"><span class="brand-mark"></span><span class="brand-name">Ferndale Estate</span></div>
  <nav class="abs main-nav">
    <span class="active">HOME</span><span>ABOUT US</span><span>LEASING</span><span>BUY</span><span>SELL</span><span>OUR TEAM</span><span>BLOG</span><span>CONTACT US</span>
  </nav>
  <div class="abs search-btn">
    <svg width="40" height="40"><circle cx="19" cy="19" r="5" fill="none" stroke="#222" stroke-width="2"/><line x1="23" y1="23" x2="26" y2="26" stroke="#222" stroke-width="2"/></svg>
  </div>
</header>

<div class="abs hero-title display"><span class="big">Ferndale</span><span class="small">Estate Collective</span></div>
<div class="abs hero-btn">GET STARTED &#8594;</div>
<div class="abs slide-arrow" style="left:63px"><svg width="48" height="48"><polyline points="28,15 19,24 28,33" fill="none" stroke="#fff" stroke-width="2.5"/></svg></div>
<div class="abs slide-arrow" style="left:1088px"><svg width="48" height="48"><polyline points="20,15 29,24 20,33" fill="none" stroke="#fff" stroke-width="2.5"/></svg></div>

<svg class="abs" style="left:0;top:0" width="600" height="1300" role="img" aria-label="Photo of a modern white home with glass doors beside a pool">
  <defs><linearGradient id="aboutTone" x1="0" y1="0" x2="1" y2="1">
    <stop offset="0" stop-color="#6f9bd6"/><stop offset=".45" stop-color="#dedbd3"/><stop offset=".8" stop-color="#cfcac0"/><stop offset="1" stop-color="#3c8a7a"/>
  </linearGradient></defs>
  <polygon points="111,796 600,764 600,1244 111,1276" fill="url(#aboutTone)"/>
</svg>

<section class="abs about-copy">
  <h2 class="display">Ferndale – a home for &ldquo;every chapter&rdquo;</h2>
  <p>Ferndale Estate Collective is built around the idea of home, the place where life happens. Buying a property is one of the most expensive and important decisions people make. We are a real estate company located in Ferndale, Canberra.</p>
  <p>Being a portfolio sales agent and property manager, coupled with our high–profile international real estate experience, Ferndale is considered a market leader on the cutting edge with deep industry knowledge, ranging from landlord–tenant relationships, residential purchases.</p>
  <span class="learn-btn">LEARN MORE &#10148;</span>
</section>

<h2 class="abs listing-title display">This month at Ferndale<br>Estate Collective</h2>
<nav class="abs filter-tabs"><span class="active">ALL</span><span>FOR SALE</span><span>FOR LEASE</span><span>OPEN TIMES</span><span>SOLD</span><span>LEASED</span></nav>
<div class="abs listing-panel"></div>

<article class="abs listing-card" style="left:127px">
  <div class="listing-photo" role="img" aria-label="Photo of a rooftop infinity pool beside an apartment tower" style="background:linear-gradient(180deg,#b9cde3 0%,#8fa3b3 45%,#2d58b8 70%,#2048a8 100%)"></div>
  <div class="listing-info">
    <h3>Level 3/18/2 Wattlebrook<br>Avenue Ferndale</h3>
    <div class="listing-stats"><span>&#9644; 2</span><span>&#9635; 2</span><span>&#9641; 1</span></div>
  </div>
</article>
<article class="abs listing-card" style="left:607px">
  <div class="listing-photo" role="img" aria-label="Photo of a white apartment building with balconies and trees" style="background:linear-gradient(180deg,#3b82d8 0%,#c9d6e2 40%,#e6e6e6 70%,#5c6a4c 100%)"></div>
  <div class="listing-info">
    <h3>96/40 Harbour Street<br>Millbrook</h3>
    <div class="listing-stats"><span>&#9644; 1</span><span>&#9635; 1</span><span>&#9641; 1</span></div>
  </div>
</article>

<h2 class="abs testimonials-title display">Testimonials</h2>
<div class="abs quote-side" style="left:50px;width:194px;text-align:left;padding-left:10px">They are a greatly professional, organized and understanding of the local feedback in a simple language and we were very pleased with anyone buying, selling</div>
<div class="abs quote-side" style="left:955px;width:200px;text-align:left">m with extensive knowledge re provided with excellent throughout the house journey nd Ferndale estate group to ent in the local area.</div>
<svg class="abs" style="left:198px;top:2330px" width="48" height="30" aria-hidden="true"><line x1="4" y1="15" x2="46" y2="15" stroke="#111" stroke-width="2"/><polyline points="16,3 4,15 16,27" fill="none" stroke="#111" stroke-width="2"/></svg>
<svg class="abs" style="left:954px;top:2330px" width="48" height="30" aria-hidden="true"><line x1="2" y1="15" x2="44" y2="15" stroke="#111" stroke-width="2"/><polyline points="32,3 44,15 32,27" fill="none" stroke="#111" stroke-width="2"/></svg>
<blockquote class="abs quote-card">
  <p>They are a greatly professional, organized and experienced team with extensive knowledge and understanding of the local market. My husband and I were provided with excellent feedback in a simple language we could understand and advice throughout the house journey and we were very pleased with the results. We highly recommend Ferndale Estate Collective to anyone buying, selling or In need of property management in the local area.</p>
  <h4>MARA HOLT</h4>
</blockquote>

<div class="abs newsletter"><span>Email address</span><div class="sub-btn">SUBSCRIBE</div></div>

<div class="abs footer-col" style="left:137px">
  <h5>Links</h5>
  <ul><li>Home</li><li>Services</li><li>Testimonials</li><li>Contact</li></ul>
</div>
<div class="abs footer-divider" style="left:336px"></div>
<div class="abs footer-col" style="left:461px;width:320px">
  <h5>Contact us</h5>
  <ul>
    <li><svg width="14" height="28" aria-hidden="true"><path d="M7 8a4 4 0 0 1 4 4c0 3-4 8-4 8s-4-5-4-8a4 4 0 0 1 4-4z" fill="#fff"/></svg><span>214/7 Wattlebrook Ave, Ferndale, ACT,<br>2960</span></li>
    <li><svg width="14" height="28" aria-hidden="true"><path d="M3 9l3-1 2 4-2 1a8 8 0 0 0 4 4l1-2 4 2-1 3c-6 0-11-5-11-11z" fill="#fff"/></svg><span>02 6000 4127</span></li>
    <li><svg width="14" height="28" aria-hidden="true"><rect x="1" y="10" width="13" height="9" fill="#fff"/><polyline points="1,10 7.5,15 14,10" fill="none" stroke="#243447" stroke-width="1.2"/></svg><span>info@companyname.com</span></li>
  </ul>
</div>
<div class="abs footer-divider" style="left:817px"></div>
<div class="abs footer-col" style="left:943px"><h5>Follow us</h5></div>
<div class="abs social" style="left:899px"></div>
<div class="abs social" style="left:944px"></div>
<div class="abs social" style="left:990px"></div>
<div class="abs social" style="left:1036px"></div>

<p class="abs copyright">&copy; Copyrights.2022 The Company Name.All Rights Reserved</p>

</body>
</html>
```